KVOR Individual and Corporate Development Business Card Design

KVOR needs a business card design that is aligned with it's values and targetted markets. Coherent Lattice of Adaptive Reasoning Method's self diagnosis model and tools, which can be used for personal improvement and team/business performance enhancement, is based on the learnings of over 20 years of medical practitioning. KVOR supercharges personal effectiveness and awareness to also increase team and business performance.

The targetted markets are high performance individuals and teams who aspire seek to enhance their capabilities and achieve their absolute best potential.

Look and feel for the business card design we are looking for is high technology, premium, fresh, new and medical.

Target Market(s)

Industry/Entity Type

Business Consultant

Contact Information for Business Card

Logo, Full Name, Title, Phone number, Email, company name, Address,

Font styles to use
Sans Serif

Requirements
Must have
• Tag line: Sharpening Potential for Consistently Driven Teams
• Please use same colours as the logo.

```html
<!DOCTYPE html>
<html lang="en">
<head>
<meta charset="utf-8">
<title>KVOR Business Card</title>
<link rel="stylesheet" href="https://fonts.googleapis.com/css2?family=Open+Sans:wght@400;600;700&display=swap">
<style>
  :root {
    --teal: #2fa7b9;
    --teal-band: #3a9fb0;
    --charcoal: #2a2b2d;
    --slate: #565b62;
    --ink: #2e2e30;
    --rule: #8c8f93;
    --backdrop: #e9e7e3;
    --paper: #ffffff;
  }
  * { box-sizing: border-box; margin: 0; padding: 0; }
  html, body { width: 1200px; height: 900px; overflow: hidden; }
  body {
    background: var(--backdrop);
    font-family: "Open Sans", Arial, sans-serif;
    display: flex;
    flex-direction: column;
    align-items: center;
    justify-content: center;
    gap: 40px;
  }
  .card {
    position: relative;
    width: 660px;
    height: 377px;
    overflow: hidden;
    box-shadow: 0 6px 18px rgba(0,0,0,0.18);
  }

  /* Back of card */
  .card-back { background: var(--charcoal); }
  .card-back .brand-mark {
    position: absolute;
    left: 0; right: 0; top: 62px;
    text-align: center;
    font-weight: 700;
    font-size: 92px;
    letter-spacing: 6px;
    color: var(--paper);
    line-height: 1;
  }
  .card-back .brand-rule {
    position: absolute;
    left: 110px; right: 110px; top: 170px;
    height: 2px;
    background: var(--rule);
  }
  .card-back .tagline-band {
    position: absolute;
    left: 0; right: 0; top: 210px;
    height: 110px;
    background: var(--teal-band);
    display: flex;
    align-items: center;
    justify-content: center;
    text-align: center;
    color: var(--paper);
    font-weight: 700;
    font-size: 20px;
    line-height: 1.3;
    text-transform: uppercase;
    letter-spacing: 0.5px;
  }

  /* Front of card */
  .card-front { background: var(--paper); }
  .card-front .corner-mark { position: absolute; left: 0; top: 0; }
  .card-front .holder {
    position: absolute;
    left: 68px; top: 24px;
  }
  .holder .holder-name {
    color: var(--teal);
    font-weight: 700;
    font-size: 19px;
    letter-spacing: 0.5px;
    text-transform: uppercase;
  }
  .holder .holder-title {
    color: var(--ink);
    font-size: 13px;
  }
  .card-front .contact {
    position: absolute;
    left: 40px; top: 140px;
    color: var(--ink);
    font-size: 15px;
    line-height: 1.3;
  }
  .contact .company { color: var(--teal); font-size: 15px; }
  .contact .address { margin-bottom: 12px; }
  .contact ul { list-style: none; }
  .contact li { display: flex; align-items: center; gap: 9px; }
  .contact svg { width: 11px; height: 11px; fill: var(--ink); flex: none; }

  .card-front .brand {
    position: absolute;
    left: 330px; top: 150px;
    width: 290px;
    text-align: center;
    color: var(--teal);
    font-weight: 700;
  }
  .brand .brand-name {
    font-size: 78px;
    letter-spacing: 5px;
    line-height: 1;
  }
  .brand .brand-rule {
    height: 2px;
    background: #c9cbcd;
    margin: 6px 0 6px;
  }
  .brand .brand-descriptor {
    font-size: 14px;
    line-height: 1.15;
    text-transform: uppercase;
    letter-spacing: 0.5px;
  }
  .card-front .footer-bands { position: absolute; left: 0; bottom: 0; }
</style>
</head>
<body>

  <section class="card card-back" aria-label="Card back">
    <div class="brand-mark">KVOR</div>
    <div class="brand-rule"></div>
    <div class="tagline-band">
      <p>Sharpening Potential<br>for Consistently Driven Teams</p>
    </div>
  </section>

  <section class="card card-front" aria-label="Card front">
    <svg class="corner-mark" width="50" height="50" viewBox="0 0 50 50" aria-hidden="true">
      <polygon points="0,0 44,0 44,44 0,44" fill="var(--slate)"/>
      <polygon points="0,44 34,0 0,0" fill="var(--paper)"/>
    </svg>

    <div class="holder">
      <p class="holder-name">Marcus Ellery</p>
      <p class="holder-title">Managing Director</p>
    </div>

    <div class="contact">
      <p class="company">KVOR</p>
      <p class="address">Address line one here,<br>Address line two here.</p>
      <ul>
        <li>
          <svg viewBox="0 0 12 12" aria-hidden="true"><rect x="3" y="0" width="6" height="12" rx="1.2"/><rect x="4" y="1.5" width="4" height="7.5" fill="#fff"/></svg>
          888 555 010
        </li>
        <li>
          <svg viewBox="0 0 12 12" aria-hidden="true"><rect x="0" y="2" width="12" height="8"/><polyline points="0.5,2.5 6,7 11.5,2.5" fill="none" stroke="#fff" stroke-width="1"/></svg>
          info@kvor.com
        </li>
        <li>
          <svg viewBox="0 0 12 12" aria-hidden="true"><circle cx="6" cy="6" r="5.5"/><ellipse cx="6" cy="6" rx="2.2" ry="5" fill="none" stroke="#fff" stroke-width="0.8"/><line x1="1" y1="6" x2="11" y2="6" stroke="#fff" stroke-width="0.8"/></svg>
          www.kvor.com
        </li>
      </ul>
    </div>

    <div class="brand">
      <p class="brand-name">KVOR</p>
      <div class="brand-rule"></div>
      <p class="brand-descriptor">Coherent Lattice of<br>Adaptive Reasoning Method</p>
    </div>

    <svg class="footer-bands" width="660" height="80" viewBox="0 0 660 80" aria-hidden="true">
      <polygon points="0,8 290,8 272,30 0,30" fill="var(--teal)"/>
      <polygon points="282,30 660,30 660,80 240,80" fill="var(--slate)"/>
    </svg>
  </section>

</body>
</html>
```